Brightwick Music Studio needs a promotional postcard design

We are looking for a postcard design for a small business that provides clients with private music lesson instruction. We are looking for a design that will convey the message of "music is fun for kids" that will appeal to parents and encourage them to sign up. We have a company logo that should be used and our color scheme is teal and turquoise. All of our contact info should be displayed as well.

Target Market(s)

Parents with young kids

Contact Information for Business Card

web: www.brightwickmusicstudio.example
email: lessons@brightwickmusicstudio.example
phone: 202-555-0147

Font styles to use
Serif
Sans Serif

Colors
33b8a4
86cfc6
0456a4
87cfc6

Requirements
Must have
• Music lessons in your home
• Creating little stars one at a time
• Sign Up Now
• Please use these images:
Nice to have
• Something like this sample postcard:

```html
<!DOCTYPE html>
<html lang="en">
<head>
<meta charset="utf-8">
<title>Brightwick Music Studio – Postcard</title>
<link rel="stylesheet" href="https://fonts.googleapis.com/css2?family=Cinzel:wght@400&family=Oswald:wght@300&display=swap">
<style>
  :root {
    --backdrop: #5e5e5e;
    --teal: #4fb8bd;
    --teal-deep: #3aaeb4;
    --peach: #f5e1d0;
    --ink: #2a2522;
    --stage-black: #0b0b0c;
    --white: #ffffff;
    --stamp: #e1e1e1;
    --rule: #9a9a9a;
  }
  * { box-sizing: border-box; margin: 0; padding: 0; }
  html, body { width: 1200px; height: 802px; overflow: hidden; }
  body { background: var(--backdrop); position: relative; }

  .postcard {
    position: absolute;
    top: 275px;
    width: 443px;
    height: 264px;
    overflow: hidden;
  }
  .postcard--front { left: 136px; background: var(--peach); }
  .postcard--back { left: 624px; background: var(--white); }

  /* Front */
  .hero-photo {
    position: absolute; left: 0; top: 0; width: 203px; height: 264px;
    background: radial-gradient(ellipse at 40% 55%, #3a2a26 0%, #151213 45%, var(--stage-black) 80%);
  }
  .framed-photo {
    position: absolute;
    border: 4px solid var(--white);
  }
  .framed-photo--portrait {
    left: 132px; top: 16px; width: 72px; height: 94px;
    background: linear-gradient(160deg, #8a6a4e, #3b2f2a 70%);
  }
  .framed-photo--piano {
    left: 156px; top: 128px; width: 93px; height: 124px;
    background: linear-gradient(180deg, #14142a 0%, #1b1b30 60%, #c9a67a 100%);
  }
  .brand {
    position: absolute; left: 232px; top: 29px;
    display: flex; align-items: center; gap: 12px;
  }
  .brand__dot {
    width: 55px; height: 55px; border-radius: 50%;
    background: var(--teal-deep); flex: none;
  }
  .brand__name {
    font-family: "Cinzel", serif; font-weight: 400;
    font-size: 17px; line-height: 1.2; color: var(--teal-deep);
  }
  .headline {
    position: absolute; left: 258px; width: 164px; top: 122px;
    font-family: "Cinzel", serif; font-weight: 400;
    text-align: center; line-height: 42px;
  }
  .headline__accent { display: block; color: var(--teal-deep); font-size: 29px; }
  .headline__line { display: block; color: var(--ink); font-size: 27px; }

  /* Back */
  .contact-panel {
    position: absolute; left: 0; top: 0; width: 240px; height: 264px;
    background: var(--teal);
  }
  .snapshot {
    position: absolute; border: 1.5px solid var(--white);
  }
  .snapshot--group { left: 14px; top: 18px; width: 77px; height: 81px;
    background: linear-gradient(180deg, #101010 0%, #2b2420 70%, #6b4c3a 100%); }
  .snapshot--recital { left: 82px; top: 35px; width: 78px; height: 83px;
    background: linear-gradient(180deg, #0f1430 0%, #1a1d35 70%, #2a2a3a 100%); }
  .snapshot--duet { left: 149px; top: 76px; width: 77px; height: 82px;
    background: linear-gradient(160deg, #6e3a22 0%, #8a4a2a 50%, #3a1c12 100%); }

  .contact-list {
    position: absolute; left: 10px; top: 164px; list-style: none;
  }
  .contact-list__item {
    display: flex; align-items: center; gap: 6px;
    height: 22px; margin-bottom: 6px;
    font-family: "Oswald", sans-serif; font-weight: 300;
    font-size: 13px; color: var(--white); letter-spacing: -0.2px;
    white-space: nowrap;
  }
  .contact-list__icon { width: 22px; height: 22px; flex: none; }

  .stamp-box {
    position: absolute; left: 362px; top: 33px; width: 54px; height: 54px;
    background: var(--stamp);
  }
  .address-line {
    position: absolute; left: 269px; width: 149px; height: 1px;
    background: var(--rule);
  }
</style>
</head>
<body>

<section class="postcard postcard--front">
  <div class="hero-photo" role="img" aria-label="Photo of a girl in a velvet dress holding a violin on stage"></div>
  <div class="framed-photo framed-photo--portrait" role="img" aria-label="Photo of a smiling young student"></div>
  <div class="framed-photo framed-photo--piano" role="img" aria-label="Photo of a girl playing a grand piano"></div>

  <div class="brand">
    <span class="brand__dot"></span>
    <span class="brand__name">Brightwick<br>Music Studio</span>
  </div>

  <h1 class="headline">
    <span class="headline__accent">MUSIC</span>
    <span class="headline__line">IS FUN</span>
    <span class="headline__line">FOR KIDS</span>
  </h1>
</section>

<section class="postcard postcard--back">
  <div class="contact-panel">
    <div class="snapshot snapshot--group" role="img" aria-label="Photo of a group of students with their teacher"></div>
    <div class="snapshot snapshot--recital" role="img" aria-label="Photo of a student at the piano during a recital"></div>
    <div class="snapshot snapshot--duet" role="img" aria-label="Photo of a student in red playing piano with a teacher"></div>

    <ul class="contact-list">
      <li class="contact-list__item">
        <svg class="contact-list__icon" viewBox="0 0 22 22" aria-hidden="true">
          <circle cx="11" cy="11" r="11" fill="#fff"/>
          <path d="M8 6.2c.5-.3 1 0 1.2.4l.8 1.8c.2.4 0 .8-.3 1l-.7.5c.5 1.2 1.4 2.2 2.6 2.8l.5-.7c.3-.3.7-.4 1-.2l1.8.9c.4.2.6.8.3 1.2l-.6.9c-.4.6-1.2.8-1.9.5-2.6-1.1-4.6-3.2-5.5-5.8-.2-.7 0-1.4.6-1.8z" fill="#4fb8bd"/>
        </svg>
        202-555-0147
      </li>
      <li class="contact-list__item">
        <svg class="contact-list__icon" viewBox="0 0 22 22" aria-hidden="true">
          <circle cx="11" cy="11" r="11" fill="#fff"/>
          <rect x="5.5" y="7.5" width="11" height="7.5" fill="none" stroke="#4fb8bd" stroke-width="1.3"/>
          <path d="M5.5 7.5l5.5 4.5 5.5-4.5" fill="none" stroke="#4fb8bd" stroke-width="1.3"/>
        </svg>
        lessons@brightwickmusicstudio.example
      </li>
      <li class="contact-list__item">
        <svg class="contact-list__icon" viewBox="0 0 22 22" aria-hidden="true">
          <circle cx="11" cy="11" r="11" fill="#fff"/>
          <circle cx="11" cy="11" r="5.5" fill="#4fb8bd"/>
          <path d="M8.5 8.5c1 .2 1.5 1 1.2 1.8-.3.7.6 1.3 1.3 1.5M12.5 6.5c-.2.8.3 1.4 1 1.5M12 15.5c.3-.9 1.2-1.4 2-1.2" fill="none" stroke="#fff" stroke-width="1"/>
        </svg>
        www.brightwickmusicstudio.example
      </li>
    </ul>
  </div>

  <div class="stamp-box"></div>
  <div class="address-line" style="top:141px"></div>
  <div class="address-line" style="top:169px"></div>
  <div class="address-line" style="top:197px"></div>
  <div class="address-line" style="top:228px"></div>
</section>

</body>
</html>
```